Silver Bloom Marisol's Cleaning Service Business Cards Project

A business card with all contact details with logo design on there (already have a logo) eye catching Logo and contact info on one side, full logo on the back, must target upper class residential and corporate companies, fitness companies, still keep it on the feminine side of things , must look elegant

Target Market(s)

Upper class homes and corporate companies

Industry/Entity Type

Cleaning Service

Contact Information for Business Card

Name: Marisol Quenby
Position: Director
ABN: 31647209853
Email: marisolssilvercleaning@tidymail.example
Number: 0417906354

Font styles to use
Decorative

Colors

Designer to choose colors to be used in the design.

Requirements
Must have
• Available Sydney Wide, contact info and logo on one side, full logo on the back
Nice to have
• Professional appearance
Should not have
• Cheap advert looking stuff

```html
<!DOCTYPE html>
<html lang="en">
<head>
<meta charset="utf-8">
<title>Silver Bloom Marisol's Cleaning Service — Business Cards</title>
<link href="https://fonts.googleapis.com/css2?family=Bitter:wght@500;600&family=Roboto:wght@400&display=swap" rel="stylesheet">
<style>
  :root {
    --backdrop: #2b2b2c;
    --card: #1d1d1e;
    --card-edge: #262627;
    --emboss: #2e2e2f;
    --teal: #6fd0cc;
    --white: #f2f2f2;
  }
  * { margin: 0; padding: 0; box-sizing: border-box; }
  html, body {
    width: 1200px; height: 900px; overflow: hidden;
    background: var(--backdrop);
  }
  .stage {
    position: relative; width: 1200px; height: 900px;
  }
  .card {
    position: absolute; left: 260px;
    width: 680px; height: 388px;
    background: var(--card);
    border: 1px solid var(--card-edge);
    overflow: hidden;
  }
  .card--back { top: 44px; }
  .card--front { top: 468px; }

  /* back: full brand name, tone-on-tone */
  .back-brand {
    position: absolute; inset: 0;
    display: flex; flex-direction: column; align-items: center; justify-content: center;
    gap: 10px;
    font-family: "Bitter", Georgia, serif; font-weight: 600;
    color: var(--emboss);
    text-transform: uppercase; text-align: center;
  }
  .back-brand__name { font-size: 46px; letter-spacing: 3px; }
  .back-brand__tagline { font-size: 15px; letter-spacing: 6px; }

  /* front */
  .front-brand {
    position: absolute; left: 22px; top: 0; bottom: 0; width: 246px;
    display: flex; flex-direction: column; align-items: center; justify-content: center;
    gap: 6px;
    font-family: "Bitter", Georgia, serif; font-weight: 600;
    color: var(--teal);
    text-transform: uppercase; text-align: center;
  }
  .front-brand__name { font-size: 28px; letter-spacing: 2px; white-space: nowrap; }
  .front-brand__tagline { font-size: 9px; letter-spacing: 3.5px; white-space: nowrap; }

  .divider {
    position: absolute; left: 288px; top: 96px;
    width: 2px; height: 196px; background: var(--white);
  }
  .contact {
    position: absolute; left: 312px; right: 20px; top: 104px;
    font-family: "Roboto", Arial, sans-serif; color: var(--white);
    white-space: nowrap;
  }
  .contact__name {
    font-family: "Bitter", Georgia, serif; font-weight: 600;
    font-size: 28px; color: var(--teal); letter-spacing: 0.5px;
  }
  .contact__role { font-size: 16px; margin-top: 2px; letter-spacing: 0.5px; }
  .contact__abn { font-size: 16px; margin-top: 24px; letter-spacing: 0.8px; }
  .contact__abn-label { color: var(--teal); }
  .contact__line {
    display: flex; align-items: center; gap: 10px;
    font-size: 15px; letter-spacing: 0.3px; margin-top: 14px;
  }
  .contact__line + .contact__line { margin-top: 8px; }
  .contact__icon { width: 17px; height: 17px; flex: none; }
</style>
</head>
<body>
<main class="stage">

  <section class="card card--back" aria-label="Card back">
    <div class="back-brand">
      <span class="back-brand__name">Silver Bloom</span>
      <span class="back-brand__tagline">Marisol's Cleaning Service</span>
    </div>
  </section>

  <section class="card card--front" aria-label="Card front">
    <div class="front-brand">
      <span class="front-brand__name">Silver Bloom</span>
      <span class="front-brand__tagline">Marisol's Cleaning Service</span>
    </div>

    <div class="divider"></div>

    <div class="contact">
      <p class="contact__name">Marisol Quenby</p>
      <p class="contact__role">Director</p>
      <p class="contact__abn"><span class="contact__abn-label">ABN :</span> 31647209853</p>
      <p class="contact__line">
        <svg class="contact__icon" viewBox="0 0 24 24" aria-hidden="true">
          <path d="M6.6 10.8a15 15 0 0 0 6.6 6.6l2.2-2.2a1 1 0 0 1 1-.25 11.4 11.4 0 0 0 3.6.57 1 1 0 0 1 1 1V20a1 1 0 0 1-1 1A17 17 0 0 1 3 4a1 1 0 0 1 1-1h3.5a1 1 0 0 1 1 1c0 1.25.2 2.45.57 3.57a1 1 0 0 1-.25 1z" fill="var(--teal)"/>
        </svg>
        0417906354
      </p>
      <p class="contact__line">
        <svg class="contact__icon" viewBox="0 0 24 24" aria-hidden="true">
          <rect x="2.5" y="5" width="19" height="14" fill="none" stroke="var(--teal)" stroke-width="1.6"/>
          <path d="M2.5 5l9.5 8 9.5-8" fill="none" stroke="var(--teal)" stroke-width="1.6"/>
        </svg>
        marisolssilvercleaning@tidymail.example
      </p>
    </div>
  </section>

</main>
</body>
</html>
```